Tollen Ridge Canvas Camps

I am Moving from nest QiV and Qelt to host my own website to create direct bookings. I haves booking platform, I just need a website to embed it into. I want a catchy website to attract potential guests to book at my accommodation located near morvane national park in Alberta, Canada.

Here is my nest QiV links:
https://www.nestqiv.ca/rooms/2048613927465105319?viralityEntryPoint=1&s=76

https://www.nestqiv.ca/rooms/2093547718260493127?viralityEntryPoint=1&s=76

https://www.nestqiv.ca/rooms/2184736590218374662?viralityEntryPoint=1&s=76

https://www.nestqiv.ca/rooms/2065128834710952483?viralityEntryPoint=1&s=76

https://www.nestqiv.ca/rooms/2317465098321857704?viralityEntryPoint=1&s=76

```html
<!DOCTYPE html>
<html lang="en">
<head>
<meta charset="utf-8">
<title>Tollen Ridge Canvas Camps</title>
<link href="https://fonts.googleapis.com/css2?family=Roboto:wght@400;500;700&display=swap" rel="stylesheet">
<style>
:root{
  --page:#f6f2ee;
  --brown:#3b2a22;
  --brown-deep:#3d2c25;
  --panel:#d9d0c9;
  --text:#2b2018;
  --muted:#5a4e47;
  --white:#ffffff;
  --line:#bfb3aa;
  --accent:#8a5a44;
}
*{box-sizing:border-box;margin:0;padding:0}
html,body{width:1200px;height:3859px;overflow:hidden}
body{position:relative;background:var(--page);font-family:'Roboto',sans-serif;color:var(--text)}
.abs{position:absolute}
.center{left:0;width:1200px;text-align:center}

/* header */
.brand{left:112px;top:20px;width:140px;display:flex;flex-direction:column;align-items:center;gap:6px}
.brand-mark{width:46px;height:46px;border-radius:50%;background:var(--brown)}
.brand-name{font-size:13px;font-weight:700;color:var(--brown);text-align:center;line-height:1.15;text-transform:uppercase}
.nav a{position:absolute;top:49px;font-size:15px;color:var(--text);text-decoration:none}
.nav a.active{font-weight:700;border-bottom:2px solid var(--text)}
.btn{background:var(--brown);color:var(--white);border-radius:20px;display:flex;align-items:center;justify-content:center;font-weight:500}
.book-now{left:971px;top:42px;width:117px;height:33px;font-size:15px}

/* hero */
.hero{left:40px;top:121px;width:1118px;height:609px;border-radius:32px;overflow:hidden;
  background:linear-gradient(180deg,#4f6a7a 0%,#7b96a3 30%,#55705a 60%,#7a6a58 85%,#5c4e43 100%)}
.hero-title{top:236px;font-size:43px;font-weight:500;color:var(--white)}
.hero-sub{top:304px;font-size:16.5px;color:var(--white)}
.hero-btn{left:527px;top:347px;width:146px;height:32px;background:var(--white);color:var(--text);border-radius:16px;font-size:15px;font-weight:500;display:flex;align-items:center;justify-content:center}

/* section heads */
.eyebrow{font-size:21px;color:var(--text)}
.h2{font-size:36px;font-weight:500;color:var(--brown)}
.lede{font-size:15px;line-height:30px;color:var(--muted)}

/* stats */
.photo{border-radius:16px;overflow:hidden}
.card{background:var(--white);border-radius:16px;padding:22px 25px}
.card-title{font-size:15px;color:var(--text);padding-bottom:10px;border-bottom:1.5px solid var(--muted)}
.card-icon{margin-top:26px;height:60px}
.card-num{margin-top:12px;font-size:31px;font-weight:700;color:var(--brown)}
.card-num span{color:var(--accent)}
.card-note{margin-top:4px;font-size:13px;color:var(--muted)}

/* reserve */
.reserve{left:61px;top:1649px;width:1077px;height:489px;background:var(--panel);border-radius:34px}
.booking{left:111px;top:1920px;width:977px;height:140px;background:var(--white);border-radius:28px}
.field-label{top:1955px;font-size:15px;color:var(--text)}
.field{top:1989px;width:165px;height:33px;border:1px solid #ddd6d0;border-radius:17px;background:#f7f4f1;font-size:12px;padding-left:14px;display:flex;align-items:center;color:var(--muted)}
.check{left:894px;top:1989px;width:164px;height:33px;font-size:15px}

/* gallery */
.tab{top:2467px;font-size:15px;color:var(--text)}
.tab-active{left:416px;top:2461px;width:104px;height:33px;font-size:15px}

/* faq */
.faq{left:61px;top:3077px;width:1077px;height:434px;background:var(--panel);border-radius:34px}
.faq-item{left:652px;width:436px;height:44px;border-bottom:1.5px solid var(--line);display:flex;justify-content:space-between;align-items:center;font-size:14px;color:var(--muted);padding:0 4px 0 2px}

/* footer */
.footer{left:0;top:3432px;width:1200px;height:427px;background:var(--brown-deep)}
.foot-brand{left:112px;top:3600px;width:225px;display:flex;flex-direction:column;align-items:center;gap:12px}
.foot-mark{width:90px;height:90px;border-radius:50%;background:var(--white)}
.foot-name{font-size:20px;font-weight:700;color:var(--white);text-transform:uppercase;text-align:center;line-height:1.2}
.contact-title{left:783px;top:3627px;font-size:20px;font-weight:500;color:var(--white)}
.contact-line{left:783px;font-size:15px;color:var(--white);display:flex;align-items:center;gap:10px}
.divider{left:111px;top:3787px;width:977px;height:1.5px;background:#8e7d72}
.copyright{top:3813px;font-size:15px;color:var(--white)}
</style>
</head>
<body>

<header>
  <div class="abs brand"><div class="brand-mark"></div><div class="brand-name">Tollen Ridge Canvas Camps</div></div>
  <nav class="nav">
    <a class="active" style="left:510px" href="#">Home</a>
    <a style="left:586px" href="#">Our Domes</a>
    <a style="left:698px" href="#">Gallery</a>
    <a style="left:780px" href="#">Reviews</a>
    <a style="left:872px" href="#">Contact</a>
  </nav>
  <div class="abs btn book-now">Book Now</div>
</header>

<section>
  <div class="abs hero" role="img" aria-label="White geodesic glamping dome on a wooden deck with red chairs, overlooking a forested valley and mountains under a cloudy sky"></div>
  <h1 class="abs center hero-title">Sleep Under the Stars at the Gateway to Morvane</h1>
  <p class="abs center hero-sub">Luxury glamping domes just minutes from Morvane National Park—where comfort meets the wild.</p>
  <div class="abs hero-btn">Explore More</div>
</section>

<section>
  <p class="abs center eyebrow" style="top:810px">Enjoy Your Stay</p>
  <h2 class="abs center h2" style="top:846px">Welcome To Tollen Ridge Canvas Camps</h2>
  <p class="abs center lede" style="top:911px">Lorem ipsum dolor sit amet, consectetur adipiscing elit, sed do eiusmod tempor incididunt ut labore et dolore magna aliqua.<br>Ut enim ad minim veniam, quis nostrud exercitation ullamco laboris nisi ut aliquip ex</p>

  <div class="abs photo" style="left:111px;top:1025px;width:488px;height:525px;background:linear-gradient(180deg,#27384a 0%,#34483f 45%,#8a6a3e 70%,#4a4038 100%)" role="img" aria-label="Glowing glamping dome on a raised deck among pine trees at night"></div>

  <div class="abs card" style="left:626px;top:1025px;width:217px;height:251px">
    <div class="card-title">Total Glamping</div>
    <svg class="card-icon" width="86" height="60" viewBox="0 0 86 60"><path d="M3 54 A40 40 0 0 1 83 54 Z" fill="var(--muted)"/><g stroke="#fff" stroke-width="2" fill="none"><path d="M43 14 L20 54 M43 14 L66 54 M10 36 L76 36 M25 22 L61 22 M43 14 L43 54"/></g><rect x="0" y="53" width="86" height="4" fill="var(--muted)"/></svg>
    <div class="card-num">60 <span>+</span></div>
    <div class="card-note">Luxury rooms &amp; suites</div>
  </div>

  <div class="abs card" style="left:871px;top:1025px;width:217px;height:251px">
    <div class="card-title">Yearly Visitors</div>
    <svg class="card-icon" width="60" height="60" viewBox="0 0 60 60"><circle cx="29" cy="30" r="28" fill="var(--brown)"/><circle cx="24" cy="23" r="7" fill="#fff"/><circle cx="37" cy="25" r="5.5" fill="#fff"/><path d="M12 44 a12 11 0 0 1 24 0 Z" fill="#fff"/><path d="M32 44 a9 9 0 0 1 16 -3 v3 Z" fill="#fff"/></svg>
    <div class="card-num">8500 <span>+</span></div>
    <div class="card-note">Happy guests</div>
  </div>

  <div class="abs card" style="left:626px;top:1299px;width:217px;height:251px">
    <div class="card-title">Signature Menu</div>
    <svg class="card-icon" width="60" height="60" viewBox="0 0 60 60"><rect x="22" y="4" width="34" height="50" rx="3" fill="var(--brown)"/><g stroke="#fff" stroke-width="2.5"><line x1="36" y1="14" x2="50" y2="14"/><line x1="36" y1="22" x2="50" y2="22"/></g><path d="M2 50 a17 16 0 0 1 34 0 Z" fill="var(--brown)" stroke="#fff" stroke-width="2"/><rect x="0" y="50" width="38" height="5" fill="var(--brown)"/><circle cx="19" cy="31" r="3" fill="var(--brown)"/></svg>
    <div class="card-num">65 <span>+</span></div>
    <div class="card-note">Curated dishes &amp; beverages</div>
  </div>

  <div class="abs photo" style="left:871px;top:1299px;width:217px;height:251px;background:linear-gradient(160deg,#8a7a5c 0%,#a86b6a 45%,#2f5448 100%)" role="img" aria-label="Guest relaxing with a cup of coffee on a dome deck"></div>
</section>

<section>
  <div class="abs reserve"></div>
  <p class="abs center eyebrow" style="top:1724px">Stay Wild Comfortably</p>
  <h2 class="abs center h2" style="top:1760px">Reserve Your Luxury Dome</h2>
  <p class="abs center lede" style="top:1825px">Lorem ipsum dolor sit amet, consectetur adipiscing elit, sed do eiusmod tempor incididunt ut labore et dolore magna aliqua.<br>Ut enim ad minim veniam, quis nostrud exercitation ullamco laboris nisi ut aliquip ex</p>
  <div class="abs booking"></div>
  <span class="abs field-label" style="left:142px">Check In</span>
  <span class="abs field-label" style="left:330px">Check Out</span>
  <span class="abs field-label" style="left:518px">Glamping Domes</span>
  <span class="abs field-label" style="left:707px">Guests</span>
  <div class="abs field" style="left:142px">Feb 18,2026</div>
  <div class="abs field" style="left:330px">Feb 19,2026</div>
  <div class="abs field" style="left:518px">1</div>
  <div class="abs field" style="left:707px">1</div>
  <div class="abs btn check">Check Availabity</div>
</section>

<section>
  <p class="abs eyebrow" style="left:110px;top:2233px">Our Gallery</p>
  <h2 class="abs h2" style="left:109px;top:2270px;font-size:37px;line-height:43px;width:480px">Experience Comfort, Elegance, and Exceptional Hospitality</h2>
  <p class="abs lede" style="left:611px;top:2269px;width:477px;line-height:29.5px;text-align:justify">Lorem ipsum dolor sit amet, consectetur adipiscing elit, sed do eiusmod tempor incididunt ut labore et dolore magna aliqua. Ut enim minim veniam, quis nostrud exercitation ullamco laboris nisi ut aliquip ex ea commodo consequat. Duis aute irure dolor in reprehenderit in voluptate velit esse cillum dolore eu fugiat nulla pariatu</p>

  <div class="abs btn tab-active">View All</div>
  <span class="abs tab" style="left:560px">Room</span>
  <span class="abs tab" style="left:641px">Dining</span>
  <span class="abs tab" style="left:723px">Facilities</span>

  <div class="abs photo" style="left:109px;top:2530px;width:230px;height:211px;border-radius:10px;background:linear-gradient(180deg,#d9d1c2 0%,#b8a690 55%,#5a2a2a 100%)" role="img" aria-label="Dome interior with bed and chairs facing a window view"></div>
  <div class="abs photo" style="left:109px;top:2752px;width:230px;height:217px;border-radius:10px;background:linear-gradient(180deg,#4a4a4a 0%,#bfbfbf 50%,#8c8a86 100%)" role="img" aria-label="Bathroom with shower and sink"></div>
  <div class="abs photo" style="left:355px;top:2530px;width:325px;height:439px;border-radius:10px;background:linear-gradient(180deg,#3e4a3a 0%,#6f7a6a 45%,#b7a58c 100%)" role="img" aria-label="Clear dome among tall pine trees on a wooden deck"></div>
  <div class="abs photo" style="left:697px;top:2530px;width:392px;height:211px;border-radius:10px;background:linear-gradient(180deg,#9fb0bd 0%,#4c5a48 50%,#8a8070 100%)" role="img" aria-label="Dome and washroom cabin in a forest clearing"></div>
  <div class="abs photo" style="left:697px;top:2752px;width:150px;height:217px;border-radius:10px;background:linear-gradient(180deg,#6f7f92 0%,#c9cdd3 60%,#8090a6 100%)" role="img" aria-label="Washroom with toilet and vanity"></div>
  <div class="abs photo" style="left:861px;top:2752px;width:228px;height:217px;border-radius:10px;background:linear-gradient(180deg,#d7cdbb 0%,#b9aa92 60%,#7a2a2a 100%)" role="img" aria-label="Dome bedroom with bed and plaid chairs"></div>
</section>

<footer class="abs footer"></footer>

<section>
  <div class="abs faq"></div>
  <p class="abs eyebrow" style="left:112px;top:3159px">FAQ</p>
  <h2 class="abs h2" style="left:112px;top:3196px;line-height:43px;width:430px">Everything You Need to Know About Staying With Us</h2>
  <div class="abs faq-item" style="top:3160px">What time is check-in and check-out?<svg width="12" height="8" viewBox="0 0 12 8"><path d="M1 1l5 5 5-5" stroke="var(--muted)" stroke-width="1.8" fill="none"/></svg></div>
  <div class="abs faq-item" style="top:3204px">Do you offer airport pick-up or shuttle service?<svg width="12" height="8" viewBox="0 0 12 8"><path d="M1 1l5 5 5-5" stroke="var(--muted)" stroke-width="1.8" fill="none"/></svg></div>
  <div class="abs faq-item" style="top:3248px">Are pets allowed in the hotel?<svg width="12" height="8" viewBox="0 0 12 8"><path d="M1 1l5 5 5-5" stroke="var(--muted)" stroke-width="1.8" fill="none"/></svg></div>
  <div class="abs faq-item" style="top:3292px">Do you have free Wi-Fi?<svg width="12" height="8" viewBox="0 0 12 8"><path d="M1 1l5 5 5-5" stroke="var(--muted)" stroke-width="1.8" fill="none"/></svg></div>
  <div class="abs faq-item" style="top:3336px">What facilities are available for guests?<svg width="12" height="8" viewBox="0 0 12 8"><path d="M1 1l5 5 5-5" stroke="var(--muted)" stroke-width="1.8" fill="none"/></svg></div>
  <div class="abs faq-item" style="top:3380px">Do you offer breakfast?<svg width="12" height="8" viewBox="0 0 12 8"><path d="M1 1l5 5 5-5" stroke="var(--muted)" stroke-width="1.8" fill="none"/></svg></div>
</section>

<section>
  <div class="abs foot-brand"><div class="foot-mark"></div><div class="foot-name">Tollen Ridge Canvas Camps</div></div>
  <p class="abs contact-title">Contact Us</p>
  <p class="abs contact-line" style="top:3671px"><svg width="15" height="15" viewBox="0 0 24 24"><path fill="#fff" d="M6.6 10.8a15.1 15.1 0 0 0 6.6 6.6l2.2-2.2c.3-.3.7-.4 1-.2 1.1.4 2.3.6 3.6.6.6 0 1 .4 1 1V20c0 .6-.4 1-1 1A17 17 0 0 1 3 4c0-.6.4-1 1-1h3.5c.6 0 1 .4 1 1 0 1.3.2 2.5.6 3.6.1.3 0 .7-.2 1z"/></svg>+1 587 555 0142</p>
  <p class="abs contact-line" style="top:3700px"><svg width="15" height="12" viewBox="0 0 24 18"><rect width="24" height="18" rx="2" fill="#fff"/><path d="M1 2l11 8 11-8" stroke="var(--brown-deep)" stroke-width="2" fill="none"/></svg>info@tollenridge.com</p>
  <p class="abs contact-line" style="top:3728px"><svg width="13" height="16" viewBox="0 0 18 24"><path fill="#fff" d="M9 0a9 9 0 0 0-9 9c0 6.8 9 15 9 15s9-8.2 9-15a9 9 0 0 0-9-9zm0 12.5A3.5 3.5 0 1 1 9 5.5a3.5 3.5 0 0 1 0 7z"/></svg>Morvane National Park in Alberta, Canada.</p>
  <div class="abs divider"></div>
  <p class="abs center copyright">Copyright © 2026 Tollen Ridge Canvas Camps. All rights reserved.</p>
</section>

</body>
</html>
```